High Tech Real Estate Startup needs a business card

We are developing an innovative real estate marketing product based around advanced search and virtual reality.

We talk to people, we need business cards.

Target Market(s)

The target market is technology professionals and realtors.

Contact Information for Business Card

The information to be included will include

Name
Title
Phone Number
E-mail Address
www.zelquin.com

It should use simple iconography for each one of those fields.

Font styles to use
Other font styles liked:
• Co, Jubilat, Avenir

Colors

Designer to choose colors to be used in the design.

Requirements
Must have
• Clean aesthetic,
• Good use of negative space.
• It should use our company logo, shown in the attached file. It is able to use the negative of that logo (coloured font and white background) and I have attached other acceptable accent colours in a swatch file.
Should not have
• Should not be too busy
• No extraneous text (slogans, tag lines etc)

```html
<!DOCTYPE html>
<html lang="en">
<head>
<meta charset="utf-8">
<title>Zelquin Business Card</title>
<link rel="stylesheet" href="https://fonts.googleapis.com/css2?family=Montserrat:wght@500&family=Roboto:wght@400&display=swap">
<style>
  :root {
    --page-bg: #e7e4df;
    --card-dark: #2b2a28;
    --teal: #1fa594;
    --cream-line: #e4dccb;
    --cream-text: #d8cbb0;
    --rule: #cfc2a6;
  }
  * { margin: 0; padding: 0; box-sizing: border-box; }
  html, body {
    width: 1200px; height: 1047px; overflow: hidden;
    background: var(--page-bg);
    font-family: "Roboto", Arial, sans-serif;
  }
  .stage { position: relative; width: 1200px; height: 1047px; }
  .card {
    position: absolute; left: 100px; top: 252px;
    width: 875px; height: 475px;
    transform: scale(1.1429); transform-origin: 0 0;
    border-radius: 14px; overflow: hidden;
    background: var(--card-dark);
    box-shadow: 0 10px 30px rgba(0,0,0,0.18);
  }
  .card-header { position: absolute; inset: 0; }
  .brand-name {
    position: absolute; left: 44px; top: 124px;
    font-family: "Montserrat", Arial, sans-serif;
    font-size: 62px; font-weight: 500; letter-spacing: 1px;
    color: var(--teal); line-height: 1;
  }
  .holder {
    position: absolute; right: 42px; top: 258px; text-align: right;
    color: var(--cream-text);
  }
  .holder-name { font-size: 29px; letter-spacing: 0.5px; line-height: 1.1; }
  .holder-title { font-size: 18px; margin-top: 4px; }
  .divider {
    position: absolute; left: 45px; right: 42px; top: 329px;
    height: 2px; background: var(--rule);
  }
  .contact-list {
    position: absolute; left: 46px; top: 366px; list-style: none;
    color: var(--cream-text); font-size: 19px; letter-spacing: 0.5px;
  }
  .contact-list li { display: flex; align-items: center; height: 27px; }
  .contact-icon { width: 13px; height: 13px; margin-right: 11px; flex: none; }
  .address {
    position: absolute; right: 42px; top: 392px; text-align: right;
    color: var(--cream-text); font-size: 19px; line-height: 27px; letter-spacing: 0.5px;
    font-style: normal;
  }
</style>
</head>
<body>
<main class="stage">
  <section class="card">
    <svg class="card-header" viewBox="0 0 875 475" width="875" height="475" aria-hidden="true">
      <path class="header-fill" fill="var(--teal)"
        d="M0,0 H875 V150 C700,150 520,60 300,52 C180,48 80,60 0,70 Z"/>
      <path class="header-edge" fill="none" stroke="var(--cream-line)" stroke-width="4"
        d="M0,78 C80,68 180,56 300,60 C520,68 700,158 875,158"/>
    </svg>

    <div class="brand-name">ZELQUIN</div>

    <div class="holder">
      <div class="holder-name">DANIEL BROOKS</div>
      <div class="holder-title">Director</div>
    </div>

    <div class="divider"></div>

    <ul class="contact-list">
      <li>
        <svg class="contact-icon" viewBox="0 0 16 16" aria-hidden="true"><path fill="var(--cream-text)" d="M3.5 1.5l2.5 0.5 1 3-1.6 1.2a9 9 0 0 0 4.4 4.4L11 9l3 1 .5 2.5-2 2C7 14.5 1.5 9 1.5 3.5z"/></svg>
        +1-555-014-2298
      </li>
      <li>
        <svg class="contact-icon" viewBox="0 0 16 16" aria-hidden="true"><rect x="1.5" y="3.5" width="13" height="9" fill="none" stroke="var(--cream-text)" stroke-width="1.5"/><path d="M1.5 3.5l6.5 5 6.5-5" fill="none" stroke="var(--cream-text)" stroke-width="1.5"/></svg>
        info@zelquin.com
      </li>
      <li>
        <svg class="contact-icon" viewBox="0 0 16 16" aria-hidden="true"><circle cx="8" cy="8" r="6.5" fill="none" stroke="var(--cream-text)" stroke-width="1.4"/><ellipse cx="8" cy="8" rx="2.8" ry="6.5" fill="none" stroke="var(--cream-text)" stroke-width="1.2"/><path d="M1.5 8h13" stroke="var(--cream-text)" stroke-width="1.2"/></svg>
        www.zelquin.com
      </li>
    </ul>

    <address class="address">
      3071 Alder ridge Ln.<br>
      Franklin, TN 37064
    </address>
  </section>
</main>
</body>
</html>
```